Quill Press Oceania needs a website

We require a website design which will be different to the normal websites that you visit. The objective of this website will be a call to action on the last page which will link to our email address so customers can email us their quotation requirements.

An example of how we envisage the look and the pages turning is as a flip books for example: https://www.vidharbor.example/watch?v=KtLmPzQa7Rw&feature=vh.be

page 1: just has our logo on it with the tag "Specialist producing quality printed books to your deadline."

Page 2: Black Page with white text "Black and White Book"
These are produced either digitally or offset on a complete range of stocks

Page 3: Colour books (use an image of your choice) These are also produced either digitally or offset plus we have the choice of web presses for larger print runs

Page 4: Digital books We do have a minimum run of 50 books using this process so a one off Thesis is not economically viable using this process. In special circumstance the digital process can produce books more quickly then by using our offset printing process.

Page 5: Having the complete range of printing machines at our disposal enables you to make a perfectly informed choice for your special project.

Then we need a special quote button which takes them directly to our email link. On this page we also need to add: We have had 25 years' experience printing books saving customers time and money whilst guaranteeing quality

Page 6: Logo repeated from page one with name: Morgan Elsworth and mobile phone no 0487 552 314

- Must follow the brief exactly. Must have a turn page book. Clear, simple and concise with a touch of creative flare and must lead into a call for action which is there quotation. A unique button for quotation link...something out of the ordinary which makes someone want to get a quote.

- It would be nice to have 3D Logo on Page 1 & 6.
a unique button for quotation link...something that make someone eager to proceed.

Our main objective is that they should not leave our website without giving us a quote. Please make sure that the spelling is correct and we do not require clip art images. Continue the logo colours through the theme
Updates

here is another example www.vidharbor.example/watch?v=JbXo412TrGe Added Saturday, May 13, 2017

Target Market(s)

Schools, Universities, Self Publishers, Publishers, Graphic Designers, Conference Providers, Businesses, Corporations, Government.

Industry/Entity Type

Printing

Coding

Coded - Design and coding required

Number of Pages Required

5+ page

Font styles to use
Sans Serif

Colors
34a6d7
ec1f27
fbed22
9bcb3c
ffc214
6b449b

Requirements
Must have
• Must follow the brief exactly. Must have a turn page book. Clear, simple and concise with a touch of creative flare and must lead into a call for action which is there quotation. A unique button for quotation link...something out of the ordinary which makes someone want to get a quote. would like to see the colours of the logo use throughout
Nice to have
• 3D Logo on Page 1 & 6.
• a unique button for quotation link...something that make someone eager to proceed.
• Our main objective is that they should not leave our website without giving us a quote
Should not have
• Spelling mistakes, clip art, ordinary design

```html
<!DOCTYPE html>
<html lang="en">
<head>
<meta charset="utf-8">
<title>Quill Press Oceania – Contact Page</title>
<link rel="stylesheet" href="https://fonts.googleapis.com/css2?family=Poppins:wght@500;700&display=swap">
<style>
  :root {
    --sky-top: #c7d4f6;
    --sky-mid: #eef2fc;
    --paper: #ffffff;
    --sky-bottom: #e4ebfa;
    --ink: #1c1c1c;
    --brand-red: #ec1f27;
    --brand-purple: #6b449b;
    --brand-gold: #ffc214;
    --brand-yellow: #fbed22;
    --brand-green: #9bcb3c;
    --brand-blue: #34a6d7;
    --brand-pink: #e8317a;
    --white: #ffffff;
  }
  * { margin: 0; padding: 0; box-sizing: border-box; }
  html, body { width: 720px; height: 1200px; overflow: hidden; }
  body { font-family: "Poppins", sans-serif; background: var(--paper); }

  .page {
    position: relative;
    width: 720px;
    height: 1200px;
    overflow: hidden;
    background: linear-gradient(180deg, var(--sky-top) 0%, var(--sky-mid) 45%, var(--paper) 65%, var(--sky-bottom) 100%);
  }

  .ribbon-area {
    position: absolute;
    left: 0;
    width: 720px;
    opacity: 0.55;
  }
  .ribbon-area--top {
    top: 0;
    height: 200px;
    background: linear-gradient(90deg, var(--brand-pink), var(--brand-red) 25%, var(--brand-gold) 45%, var(--brand-yellow) 60%, var(--brand-green) 78%, var(--brand-blue));
    -webkit-mask-image: linear-gradient(180deg, #000 0%, transparent 100%);
    mask-image: linear-gradient(180deg, #000 0%, transparent 100%);
  }
  .ribbon-area--bottom {
    bottom: 0;
    height: 220px;
    background: linear-gradient(90deg, var(--brand-blue), var(--brand-green) 22%, var(--brand-yellow) 42%, var(--brand-gold) 58%, var(--brand-red) 78%, var(--brand-pink));
    -webkit-mask-image: linear-gradient(0deg, #000 0%, transparent 100%);
    mask-image: linear-gradient(0deg, #000 0%, transparent 100%);
  }

  .brand {
    position: absolute;
    top: 262px;
    left: 0;
    width: 740px;
    text-align: center;
    color: var(--ink);
  }
  .brand__mark {
    display: block;
    width: 60px;
    height: 60px;
    margin: 0 auto 34px;
    border-radius: 50%;
    background: var(--brand-blue);
  }
  .brand__name {
    font-weight: 500;
    font-size: 34px;
    line-height: 40px;
  }

  .contact-name {
    position: absolute;
    top: 500px;
    left: 0;
    width: 745px;
    text-align: center;
    font-weight: 700;
    font-size: 45px;
    line-height: 60px;
    color: var(--brand-red);
  }

  .phone-pill {
    position: absolute;
    top: 576px;
    left: 223px;
    width: 300px;
    height: 57px;
    border-radius: 29px;
    background: var(--brand-purple);
    display: flex;
    align-items: center;
    padding-left: 17px;
  }
  .phone-pill__icon { width: 36px; height: 36px; flex: none; }
  .phone-pill__number {
    margin-left: 16px;
    font-weight: 700;
    font-size: 29px;
    letter-spacing: 1px;
    color: var(--white);
  }
</style>
</head>
<body>
<main class="page">

  <div class="ribbon-area ribbon-area--top" role="img" aria-label="Decorative rainbow ribbon across the top"></div>

  <section class="brand">
    <span class="brand__mark"></span>
    <p class="brand__name">Quill Press<br>Oceania</p>
  </section>

  <h1 class="contact-name">Morgan Elsworth</h1>

  <div class="phone-pill">
    <svg class="phone-pill__icon" viewBox="0 0 36 36" aria-hidden="true">
      <circle cx="18" cy="18" r="18" fill="var(--brand-gold)"/>
      <path d="M12.5 9.5c1-.6 2-.3 2.6.6l1.5 2.5c.5.9.3 1.8-.5 2.4l-1 .7c.8 2 2.3 3.6 4.3 4.5l.8-1c.6-.8 1.6-1 2.4-.5l2.5 1.5c.9.6 1.1 1.7.5 2.6l-1 1.4c-.8 1-2.1 1.4-3.3 1-5.2-1.7-9-5.6-10.6-10.7-.4-1.2 0-2.5 1-3.3z" fill="var(--white)"/>
    </svg>
    <span class="phone-pill__number">0487 552 314</span>
  </div>

  <div class="ribbon-area ribbon-area--bottom" role="img" aria-label="Decorative rainbow ribbon across the bottom"></div>

</main>
</body>
</html>
```